Meal Plan Website Needs New Pages Designed

Brightwick Supper Kits is an online, membership based program that delivers weekly meal programs (7 days worth of recipes plus shopping lists) carefully crafted by an expert team of meal planners. All recipes are created to comply with the following macronutrient ratio: 65% healthy fats, 25% lean protein, 10% good carbs.
All recipes are Paleo friendly and a great resource for those individuals who want to correctly implement this type of diet.

We are re-designing our website and need the following pages designed:

· Home page w/ logo
· How it works page
· Get Started! page
· Recipes Page template (these will be the pages on our site that will have recipes)
· Kitchen Essentials Training page (this will be a page with videos and tips + tricks, PDFs, etc)

So 5 total PSDs, 1 for each page.

Target audience: Men and women between the ages of 30 and 60 who want to:
· Eat healthy
· Lose weight
· Follow/Implement the Paleo diet
· Take the guesswork out of preparing delicious AND healthy meals for them and their families
· Know exactly what to eat, what to buy, how to make it

Feelings/Messages we want to communicate through the design:
· “Organic” but elegant look
· Fresh/light/Airy
· Simple but NOT GENERIC
· “I want to get cooking” feeling

Our Stylistic preferences:
· Minimalist with a few bold elements (something in between)
· Easy to visually navigate (enough white space, but not too much)
· There is more to “see” than to “read”

Our Color Preferences:
· Lighter pallet
· Colors that evoke natural woods, granite countertops…
· Stay away from using all dark colors

Our Font Type Preferences:
· Easy to read
· Not more than 3 font types
· Not too rigid
· Not too sophisticated
· Simple with a touch

Examples of Website Designs that we like:
· http://www.dorvanta.com/meal-plans/
· http://grulvix.com/
· https://www.mistobarn.com/

```html
<!DOCTYPE html>
<html lang="en">
<head>
<meta charset="utf-8">
<title>Brightwick Supper Kits</title>
<link rel="stylesheet" href="https://fonts.googleapis.com/css2?family=Roboto+Condensed:wght@400;700&family=Roboto:ital,wght@0,400;0,500;1,400&display=swap">
<style>
  :root {
    --red: #d9503a;
    --red-dark: #c8412d;
    --orange: #f28a4d;
    --orange-deep: #ee7c3f;
    --peach: #f6a57c;
    --peach-light: #f4b08a;
    --wood-light: #efdcbc;
    --wood-mid: #e4c8a0;
    --wood-warm: #e9cfa8;
    --footer-wood: #6b5a48;
    --footer-edge: #5a4a3b;
    --footer-dark: #4a3d31;
    --ink: #2b2b2b;
    --white: #ffffff;
    --heading: "Roboto Condensed", "Arial Narrow", sans-serif;
    --body: "Roboto", Arial, sans-serif;
  }
  * { box-sizing: border-box; margin: 0; padding: 0; }
  html, body { width: 1200px; height: 2560px; overflow: hidden; }
  body { position: relative; font-family: var(--body); color: var(--ink); background: var(--wood-light); }

  /* Header */
  .site-header { position: absolute; left: 0; top: 0; width: 1200px; height: 78px; background: var(--white); box-shadow: 0 2px 4px rgba(0,0,0,.08); z-index: 3; }
  .brand { position: absolute; left: 172px; top: 12px; display: flex; align-items: center; gap: 10px; }
  .brand-mark { width: 53px; height: 53px; background: var(--red); border-radius: 3px; }
  .brand-name { font-family: var(--heading); font-weight: 700; font-size: 23px; color: var(--red); }
  .main-nav a { position: absolute; top: 33px; font-family: var(--heading); font-size: 13px; color: #444; text-decoration: none; text-transform: uppercase; }

  /* Side tabs */
  .side-tab { position: absolute; right: 0; width: 44px; background: var(--red); color: var(--white); font-family: var(--heading); font-size: 17px; writing-mode: vertical-rl; transform: rotate(180deg); display: flex; align-items: center; justify-content: center; text-transform: uppercase; z-index: 4; border-radius: 0 4px 4px 0; }
  .tab-login { top: 116px; height: 75px; }
  .tab-register { top: 201px; height: 120px; }

  /* Hero */
  .hero { position: absolute; left: 0; top: 78px; width: 1200px; height: 453px; background: radial-gradient(ellipse at 50% 40%, #c9a27a 0%, #a9794f 35%, #7a5a3d 60%, #e9e2d8 100%); }
  .hero-caption { position: absolute; left: 111px; top: 310px; width: 683px; height: 40px; background: #151515; color: var(--white); font-family: var(--heading); font-size: 18px; line-height: 40px; padding-left: 22px; text-transform: uppercase; white-space: nowrap; }
  .hero-arrows { position: absolute; left: 806px; top: 309px; display: flex; gap: 3px; }
  .arrow-btn { width: 40px; height: 40px; background: var(--red); display: flex; align-items: center; justify-content: center; }
  .order-btn { position: absolute; left: 111px; top: 361px; width: 133px; height: 44px; background: var(--red); color: var(--white); font-family: var(--heading); font-size: 17px; line-height: 44px; text-align: center; text-transform: uppercase; }

  /* Intro band */
  .intro-band { position: absolute; left: 0; top: 531px; width: 1200px; height: 222px; background: linear-gradient(90deg, #f2a67c, var(--peach-light) 50%, #f2a67c); text-align: center; }
  .intro-title { position: absolute; left: 0; width: 100%; top: 34px; font-family: var(--heading); font-weight: 400; font-size: 29px; color: var(--red); text-transform: uppercase; }
  .intro-divider { position: absolute; left: 540px; top: 83px; width: 120px; height: 18px; background: linear-gradient(90deg, rgba(255,255,255,0), rgba(255,255,255,.85) 50%, rgba(255,255,255,0)); }
  .intro-text { position: absolute; left: 276px; width: 648px; top: 122px; font-size: 19px; line-height: 32px; color: var(--white); }

  /* Features */
  .features { position: absolute; left: 0; top: 753px; width: 1200px; height: 473px; background: linear-gradient(90deg, var(--wood-mid), var(--wood-light) 30%, var(--wood-warm) 60%, var(--wood-light) 80%, var(--wood-mid)); }
  .section-title { position: absolute; left: 0; width: 100%; top: 54px; text-align: center; font-family: var(--heading); font-weight: 400; font-size: 29px; color: var(--red); text-transform: uppercase; }
  .feature-card { position: absolute; top: 124px; width: 244px; height: 292px; background: var(--peach); text-align: center; color: var(--white); }
  .feature-card.is-active { background: var(--red); }
  .feature-icon { position: absolute; left: 72px; top: 38px; width: 100px; height: 100px; border-radius: 50%; background: var(--white); display: flex; align-items: center; justify-content: center; }
  .feature-name { position: absolute; top: 163px; width: 100%; font-family: var(--heading); font-weight: 400; font-size: 21px; text-transform: uppercase; }
  .feature-text { position: absolute; top: 197px; left: 32px; width: 180px; font-size: 10.5px; line-height: 20.5px; }

  /* Testimonials */
  .testimonials { position: absolute; left: 0; top: 1226px; width: 1200px; height: 298px; background: linear-gradient(90deg, var(--orange-deep), var(--orange) 50%, var(--orange-deep)); }
  .client-photo { position: absolute; left: 172px; top: 47px; width: 202px; height: 202px; border-radius: 50%; border: 8px solid var(--white); background: radial-gradient(circle at 50% 40%, #d9b79a, #8e7a66 70%, #5d5a52); }
  .testimonials-title { position: absolute; left: 430px; top: 48px; font-family: var(--heading); font-weight: 400; font-size: 31px; color: var(--white); text-transform: uppercase; }
  .testimonial-arrows { position: absolute; left: 976px; top: 57px; display: flex; gap: 2px; }
  .testimonial-arrows .arrow-btn { width: 18px; height: 18px; background: var(--red-dark); }
  .quote-mark { position: absolute; font-family: Georgia, serif; font-size: 30px; color: var(--white); line-height: 1; }
  .quote-text { position: absolute; left: 457px; top: 123px; width: 510px; font-size: 10.5px; font-style: italic; line-height: 19.5px; color: var(--white); }
  .quote-author { position: absolute; left: 457px; top: 200px; font-size: 10.5px; font-style: italic; line-height: 20px; color: var(--white); }

  /* Plans grid */
  .plans { position: absolute; left: 0; top: 1524px; width: 1200px; height: 791px; background: linear-gradient(90deg, var(--wood-mid), var(--wood-light) 30%, var(--wood-warm) 60%, var(--wood-light) 80%, var(--wood-mid)); }
  .plan { position: absolute; width: 256px; }
  .plan-title { font-family: var(--heading); font-weight: 400; font-size: 23px; line-height: 32px; color: var(--red); text-transform: uppercase; height: 32px; }
  .plan-photo { width: 256px; height: 193px; position: relative; }
  .plan-text { margin-top: 17px; font-size: 10.5px; line-height: 20px; color: #333; }
  .read-more-overlay { position: absolute; inset: 0; background: rgba(222, 95, 70, 0.92); display: flex; align-items: center; justify-content: center; }
  .read-more-overlay span { font-family: var(--heading); font-size: 19px; color: var(--white); text-transform: uppercase; border-top: 1px solid rgba(255,255,255,.8); border-bottom: 1px solid rgba(255,255,255,.8); padding: 14px 30px; }

  /* Footer */
  .site-footer { position: absolute; left: 0; top: 2315px; width: 1200px; height: 203px; background: linear-gradient(90deg, var(--footer-edge), var(--footer-wood) 50%, var(--footer-edge)); color: var(--white); }
  .footer-links { position: absolute; top: 42px; width: 124px; list-style: none; }
  .footer-links li { font-size: 10px; height: 30px; line-height: 22px; border-bottom: 1px solid rgba(255,255,255,.55); }
  .footer-links li:last-child { border-bottom: none; }
  .footer-heading { position: absolute; top: 45px; font-family: var(--heading); font-weight: 400; font-size: 13px; text-transform: uppercase; }
  .news-arrows { position: absolute; left: 760px; top: 44px; font-size: 13px; letter-spacing: 6px; }
  .news-text { position: absolute; left: 575px; top: 54px; width: 212px; font-size: 10px; line-height: 20px; }
  .news-date { position: absolute; left: 575px; top: 136px; font-size: 9.5px; font-style: italic; }
  .field { position: absolute; left: 831px; width: 196px; height: 22px; background: var(--white); color: #777; font-size: 9px; line-height: 22px; padding-left: 10px; }
  .subscribe { position: absolute; left: 951px; top: 137px; font-family: var(--heading); font-size: 12px; text-transform: uppercase; }

  .footer-bar { position: absolute; left: 0; top: 2518px; width: 1200px; height: 42px; background: var(--footer-dark); color: var(--white); }
  .copyright { position: absolute; left: 172px; top: 15px; font-size: 9.5px; }
  .social { position: absolute; left: 810px; top: 16px; display: flex; gap: 24px; }
  .social span { width: 10px; height: 10px; border-radius: 50%; background: var(--white); opacity: .85; }
</style>
</head>
<body>

<header class="site-header">
  <div class="brand">
    <div class="brand-mark"></div>
    <div class="brand-name">Brightwick Supper Kits</div>
  </div>
  <nav class="main-nav">
    <a href="#" style="left:471px">Meal Plans</a>
    <a href="#" style="left:604px">About</a>
    <a href="#" style="left:710px">How It Works</a>
    <a href="#" style="left:857px">Resources</a>
    <a href="#" style="left:988px">Blog</a>
  </nav>
</header>

<div class="side-tab tab-login">Login</div>
<div class="side-tab tab-register">Register</div>

<section class="hero" role="img" aria-label="Close-up photo of whole-wheat wraps filled with tomato, cucumber and greens">
  <div class="hero-caption">We provide membership based program that delivers weekly meal programs</div>
  <div class="hero-arrows">
    <div class="arrow-btn"><svg width="12" height="16" viewBox="0 0 12 16"><path d="M9 2 3 8l6 6" fill="none" stroke="#fff" stroke-width="2"/></svg></div>
    <div class="arrow-btn"><svg width="12" height="16" viewBox="0 0 12 16"><path d="m3 2 6 6-6 6" fill="none" stroke="#fff" stroke-width="2"/></svg></div>
  </div>
  <div class="order-btn">Order Now</div>
</section>

<section class="intro-band">
  <h1 class="intro-title">Brightwick Supper Kits</h1>
  <div class="intro-divider" role="img" aria-label="Decorative flourish divider"></div>
  <p class="intro-text">All recipes are created to comply with the following macronutrient ratio: 65% healthy fats, 25% lean protein, 10% good carbs</p>
</section>

<section class="features">
  <h2 class="section-title">Everything you need to eat healthier</h2>

  <div class="feature-card is-active" style="left:196px">
    <div class="feature-icon">
      <svg width="38" height="48" viewBox="0 0 46 58"><rect x="3" y="6" width="40" height="50" rx="4" fill="none" stroke="#d9503a" stroke-width="3"/><rect x="14" y="2" width="18" height="8" rx="2" fill="#d9503a"/><path d="M10 22l3 3 5-6M10 34l3 3 5-6M10 46l3 3 5-6" fill="none" stroke="#d9503a" stroke-width="2.5"/><path d="M23 23h13M23 35h13M23 47h13" stroke="#d9503a" stroke-width="2.5"/></svg>
    </div>
    <h3 class="feature-name">Meal Plans</h3>
    <p class="feature-text">uncover many web sites still in their infancy. Various versions have evolved over the years...</p>
  </div>

  <div class="feature-card" style="left:480px">
    <div class="feature-icon">
      <svg width="56" height="45" viewBox="0 0 70 56"><circle cx="35" cy="28" r="20" fill="none" stroke="#333" stroke-width="3"/><circle cx="35" cy="28" r="13" fill="none" stroke="#333" stroke-width="2"/><path d="M6 6v14M3 6v9M9 6v9M3 15h6M6 20v32" stroke="#333" stroke-width="2.5" fill="none"/><path d="M64 4c-5 4-5 16 0 20v28" stroke="#333" stroke-width="3" fill="none"/></svg>
    </div>
    <h3 class="feature-name">Quickstart Guide</h3>
    <p class="feature-text">uncover many web sites still in their infancy. Various versions have evolved over the years...</p>
  </div>

  <div class="feature-card" style="left:763px">
    <div class="feature-icon">
      <svg width="56" height="41" viewBox="0 0 68 50"><path d="M36 22 52 8l16 14M40 20v24h24V20" fill="none" stroke="#333" stroke-width="3"/><rect x="48" y="32" width="8" height="12" fill="#333"/><path d="M2 14h6l5 20h20l4-14H12" fill="none" stroke="#333" stroke-width="3"/><circle cx="16" cy="42" r="3.5" fill="#333"/><circle cx="30" cy="42" r="3.5" fill="#333"/></svg>
    </div>
    <h3 class="feature-name">At-Home Workouts</h3>
    <p class="feature-text">uncover many web sites still in their infancy. Various versions have evolved over the years...</p>
  </div>
</section>

<section class="testimonials">
  <div class="client-photo" role="img" aria-label="Portrait photo of a smiling member"></div>
  <h2 class="testimonials-title">Testimonials</h2>
  <div class="testimonial-arrows">
    <div class="arrow-btn"><svg width="8" height="10" viewBox="0 0 8 10"><path d="M6 1 2 5l4 4" fill="none" stroke="#fff" stroke-width="1.5"/></svg></div>
    <div class="arrow-btn"><svg width="8" height="10" viewBox="0 0 8 10"><path d="m2 1 4 4-4 4" fill="none" stroke="#fff" stroke-width="1.5"/></svg></div>
  </div>
  <span class="quote-mark" style="left:433px; top:112px">&ldquo;</span>
  <p class="quote-text">It is a long established fact that a reader will be distracted by the readable content of a page when looking at its layout. The point of using Lorem Ipsum is that it has a more-or-less normal distribution of letters, as opposed to using 'Content here, content here', making it look like readable English.</p>
  <span class="quote-mark" style="left:973px; top:184px">&rdquo;</span>
  <p class="quote-author">- Maren Ostlund -<br>Event marketer</p>
</section>

<section class="plans">
  <article class="plan" style="left:171px; top:62px">
    <h3 class="plan-title">Classic</h3>
    <div class="plan-photo" role="img" aria-label="Photo of a classic meal plan dish" style="background:linear-gradient(135deg,#c98a6a,#a4533c)">
      <div class="read-more-overlay"><span>Read More</span></div>
    </div>
    <p class="plan-text">It is a long established fact that a reader will be distracted by the readable content of a page when looking at its layout. The point of using Lorem Ipsum is that it has a more-or-less normal distribution...</p>
  </article>
  <article class="plan" style="left:471px; top:62px">
    <h3 class="plan-title">For One</h3>
    <div class="plan-photo" role="img" aria-label="Photo of a fresh salad bowl with grilled peppers" style="background:radial-gradient(circle at 50% 50%,#d56a3a,#5f8a3a 55%,#d8d6cf)"></div>
    <p class="plan-text">It is a long established fact that a reader will be distracted by the readable content of a page when looking at its layout. The point of using Lorem Ipsum is that it has a more-or-less normal distribution...</p>
  </article>
  <article class="plan" style="left:771px; top:62px">
    <h3 class="plan-title">Lunch</h3>
    <div class="plan-photo" role="img" aria-label="Photo of a lunch plate with tacos, lime and salsa" style="background:radial-gradient(circle at 50% 60%,#d9a441,#8a4a25 55%,#2e3a4f)"></div>
    <p class="plan-text">It is a long established fact that a reader will be distracted by the readable content of a page when looking at its layout. The point of using Lorem Ipsum is that it has a more-or-less normal distribution...</p>
  </article>

  <article class="plan" style="left:171px; top:430px">
    <h3 class="plan-title">Kosher</h3>
    <div class="plan-photo" role="img" aria-label="Photo of grilled salmon with a green side salad" style="background:radial-gradient(circle at 40% 60%,#e07a4f,#7fa35a 50%,#f1ede6)"></div>
    <p class="plan-text">It is a long established fact that a reader will be distracted by the readable content of a page when looking at its layout. The point of using Lorem Ipsum is that it has a more-or-less normal distribution...</p>
  </article>
  <article class="plan" style="left:471px; top:430px">
    <h3 class="plan-title">Dairy Free</h3>
    <div class="plan-photo" role="img" aria-label="Photo of a baked pie with green beans and roast vegetables" style="background:radial-gradient(circle at 50% 45%,#e8b552,#7a4426 60%,#3a2a1e)"></div>
    <p class="plan-text">It is a long established fact that a reader will be distracted by the readable content of a page when looking at its layout. The point of using Lorem Ipsum is that it has a more-or-less normal distribution...</p>
  </article>
  <article class="plan" style="left:771px; top:430px">
    <h3 class="plan-title">Gluten Free</h3>
    <div class="plan-photo" role="img" aria-label="Photo of people sharing plates at a wooden dinner table" style="background:radial-gradient(circle at 50% 50%,#b5703f,#6e4630 55%,#2f3850)"></div>
    <p class="plan-text">It is a long established fact that a reader will be distracted by the readable content of a page when looking at its layout. The point of using Lorem Ipsum is that it has a more-or-less normal distribution...</p>
  </article>
</section>

<footer class="site-footer">
  <ul class="footer-links" style="left:183px">
    <li>Meal Plans</li><li>About</li><li>How it Works</li><li>Resources</li><li>Blog</li>
  </ul>
  <ul class="footer-links" style="left:379px">
    <li>Testimonials</li><li>Homes Blog</li><li>Resources</li><li>Contact</li>
  </ul>
  <h4 class="footer-heading" style="left:575px">Latest News</h4>
  <div class="news-arrows">&lsaquo;&rsaquo;</div>
  <p class="news-text">Many desktop publishing packages and web page editors now use Lorem Ipsum as their default model text...</p>
  <p class="news-date">Posted on 25 Dec 2014</p>
  <h4 class="footer-heading" style="left:831px">Newsletter Signup</h4>
  <div class="field" style="top:73px">Name :</div>
  <div class="field" style="top:102px">Email :</div>
  <div class="subscribe">Subscribe &raquo;</div>
</footer>

<div class="footer-bar">
  <p class="copyright">&copy; 2014. Brightwick Supper Kits. All rights reserved.</p>
  <div class="social">
    <span></span><span></span><span></span><span></span><span></span><span></span><span></span>
  </div>
</div>

</body>
</html>
```